business card design for a plumbing contractor

i need a double business card for a plumbing business, our initial service is residential Sewer Drain Cleaning.

Target Market(s)

other plumbing Business

Industry/Entity Type

Plumbing

Contact Information for Business Card

www.PipeworksTopMark.example- 5307218394-

Font styles to use
Serif

Colors
ec1f27
0455a3

```html
<!DOCTYPE html>
<html lang="en">
<head>
<meta charset="utf-8">
<title>Pipeworks Top Mark – Business Card</title>
<link rel="stylesheet" href="https://fonts.googleapis.com/css2?family=Roboto+Condensed:wght@400;700&display=swap">
<style>
  :root {
    --bg: #2a2a2a;
    --card-white: #f4f4f2;
    --card-red: #d7372f;
    --accent-red: #d8322b;
    --text-grey: #7a7165;
    --text-dark: #4a4a4a;
    --rule: #6f6f6f;
    --white: #ffffff;
  }
  * { margin: 0; padding: 0; box-sizing: border-box; }
  html, body {
    width: 1200px; height: 960px; overflow: hidden;
    background: var(--bg);
    font-family: "Roboto Condensed", "Arial Narrow", sans-serif;
  }
  .canvas { position: relative; width: 1200px; height: 960px; }

  .card {
    position: absolute; left: 320px; width: 600px; height: 342px;
  }
  .card--front { top: 104px; background: var(--card-white); }
  .card--back { top: 493px; background: var(--card-red); }

  .brand-name {
    position: absolute; right: 36px; top: 48px;
    font-weight: 700; font-size: 30px; line-height: 1;
    color: var(--text-grey);
    display: flex; align-items: center; gap: 10px;
  }
  .brand-name .brand-dot {
    width: 14px; height: 14px; border-radius: 50%; background: var(--accent-red);
  }

  .person { position: absolute; left: 33px; top: 198px; }
  .person__name {
    font-weight: 700; font-size: 22px; color: var(--accent-red); letter-spacing: 0.2px;
  }
  .person__role {
    font-size: 16px; color: var(--text-grey); margin-top: 2px; letter-spacing: 0.3px;
  }

  .rule {
    position: absolute; left: 33px; right: 34px; top: 250px;
    border-top: 1px solid var(--rule);
  }

  .contact {
    position: absolute; left: 36px; top: 266px;
    list-style: none; font-size: 14px; line-height: 18px; color: var(--text-dark);
  }

  .services {
    position: absolute; right: 33px; top: 265px;
    list-style: none; font-size: 15px; line-height: 18px; color: var(--text-dark);
    text-align: right;
  }
  .services li::after {
    content: ""; display: inline-block; width: 6px; height: 6px; border-radius: 50%;
    background: var(--accent-red); margin-left: 6px; vertical-align: middle;
  }

  .back-brand {
    position: absolute; left: 0; right: 0; top: 130px;
    display: flex; justify-content: center; align-items: center; gap: 14px;
    font-weight: 700; font-size: 42px; color: var(--white);
  }
  .back-brand .brand-square { width: 22px; height: 22px; background: var(--white); }

  .back-services {
    position: absolute; left: 0; right: 0; top: 284px;
    text-align: center; font-size: 15px; color: var(--white);
  }
  .back-services .sep {
    display: inline-block; width: 6px; height: 6px; border-radius: 50%;
    background: var(--white); margin: 0 5px; vertical-align: middle;
  }
</style>
</head>
<body>
<main class="canvas">
  <section class="card card--front">
    <div class="brand-name"><span>Pipeworks Top Mark</span><span class="brand-dot"></span></div>
    <div class="person">
      <p class="person__name">DANIEL REYES</p>
      <p class="person__role">CEO/FOUNDER</p>
    </div>
    <div class="rule"></div>
    <ul class="contact">
      <li>P. 5307218394</li>
      <li>Dispatch@PipeworksTopMark.example</li>
      <li>www.PipeworksTopMark.example</li>
    </ul>
    <ul class="services">
      <li>Sewer Drain Cleaning</li>
      <li>Maintenance</li>
      <li>Trenchless Pipe Installs</li>
    </ul>
  </section>

  <section class="card card--back">
    <div class="back-brand"><span>Pipeworks Top Mark</span><span class="brand-square"></span></div>
    <p class="back-services">Sewer Drain Cleaning<span class="sep"></span>Maintenance<span class="sep"></span>Trenchless Pipe Installs</p>
  </section>
</main>
</body>
</html>
```